Brindle Asset Management Vendor Recruiting Email

We need a digital flyer to email and post on Social media to attract new vendors to our website to apply to complete maintenance work on our clients homes. I have one flyer we had produced recently that we are un-happy with. It is attached.

The example given is what we do not want!! We do not want any of the pictures used from the existing one

Target Market(s)

Construction companies and handyman

Industry/Entity Type

Residential maintenance and repairs

Requirements
Must have
• Join our team as the header not become a vendor

```html
<!DOCTYPE html>
<html lang="en">
<head>
<meta charset="utf-8">
<title>Brindle Asset Management – Join Our Team</title>
<link href="https://fonts.googleapis.com/css2?family=League+Spartan:wght@600;700;800;900&family=Vollkorn:wght@600&family=Mulish:ital,wght@0,400;1,800&display=swap" rel="stylesheet">
<style>
  :root {
    --navy: #12101f;
    --purple: #5f2d94;
    --panel-top: #6a6a9e;
    --panel-bottom: #8783bf;
    --white: #ffffff;
    --ink: #111111;
    --yellow: #f5b400;
    --sky-top: #8fb6e3;
    --sky-mid: #cfe2f4;
    --grass: #5f9a36;
  }
  * { box-sizing: border-box; margin: 0; padding: 0; }
  html, body { width: 1200px; height: 1200px; overflow: hidden; background: var(--white); }
  .flyer { position: relative; width: 1200px; height: 1200px; overflow: hidden; background: var(--white); }

  .hero-photo {
    position: absolute; left: 0; top: 0; width: 1200px; height: 726px;
    background:
      linear-gradient(90deg, rgba(0,0,0,0) 55%, rgba(40,48,90,0.55) 62%, rgba(35,42,80,0.7) 100%),
      linear-gradient(180deg, var(--sky-top) 0%, var(--sky-mid) 45%, #b9c2c8 62%, #7fae52 80%, var(--grass) 100%);
  }
  .hero-band { position: absolute; left: 0; top: 718px; width: 1200px; height: 12px; background: var(--purple); }
  .bottom-band { position: absolute; left: 0; top: 1182px; width: 1200px; height: 18px; background: var(--purple); }

  .brand-box {
    position: absolute; left: 185px; top: 0; width: 305px; height: 167px;
    background: var(--navy); border-radius: 0 0 14px 14px;
    display: flex; align-items: center; justify-content: center; gap: 10px;
  }
  .brand-name {
    font-family: "League Spartan", sans-serif; font-weight: 700; font-size: 22px;
    color: var(--white); text-align: center; line-height: 1.15; letter-spacing: 1px;
  }
  .brand-dot { width: 14px; height: 14px; background: var(--white); flex: none; }

  .headline { position: absolute; left: 44px; top: 240px; font-family: "League Spartan", sans-serif; }
  .headline .lead { font-weight: 800; font-size: 78px; color: var(--ink); line-height: 1; letter-spacing: 1px; }
  .headline .key { font-weight: 800; font-size: 134px; color: var(--purple); line-height: 1; margin-top: 10px; letter-spacing: -1px; }

  .benefits-frame {
    position: absolute; left: 44px; top: 460px; width: 624px; height: 740px;
    background: var(--white); border-radius: 0 66px 0 0;
  }
  .benefits-panel {
    position: absolute; left: 53px; top: 473px; width: 605px; height: 727px;
    background: linear-gradient(180deg, var(--panel-top), var(--panel-bottom));
    border-radius: 0 56px 0 0;
  }
  .benefits { position: absolute; left: 88px; top: 508px; width: 560px; list-style: none;
    font-family: "Vollkorn", serif; font-weight: 600; font-size: 31px; line-height: 38px;
    color: var(--white); white-space: nowrap; }
  .benefits li { position: relative; padding-left: 42px; margin-bottom: 39px; }
  .benefits .tick { position: absolute; left: 0; top: 9px; width: 22px; height: 22px; }

  .contact-label {
    position: absolute; left: 183px; top: 950px; padding: 4px 20px 6px;
    background: var(--purple); color: var(--white); border-radius: 6px 6px 0 0;
    font-family: "League Spartan", sans-serif; font-weight: 700; font-size: 26px; letter-spacing: 1px;
    transform: rotate(-3deg);
  }
  .phone-box {
    position: absolute; left: 108px; top: 990px; width: 476px; height: 112px;
    background: var(--white); border: 3px solid var(--ink); border-radius: 12px;
    transform: rotate(-3deg);
    display: flex; align-items: center; justify-content: center;
    font-family: "League Spartan", sans-serif; font-weight: 800; font-size: 78px; color: var(--ink);
    letter-spacing: -2px; padding-top: 10px;
  }
  .web-bar {
    position: absolute; left: 77px; top: 1133px; width: 554px; height: 67px;
    background: var(--yellow); border-radius: 14px 14px 0 0;
    display: flex; align-items: center; justify-content: center; padding-bottom: 4px;
    font-family: "Mulish", sans-serif; font-style: italic; font-weight: 800; font-size: 27px; color: var(--ink);
  }

  .requirements { position: absolute; left: 699px; top: 744px; width: 495px; }
  .requirements h2 {
    font-family: "League Spartan", sans-serif; font-weight: 900; font-size: 45px; line-height: 49px;
    color: var(--purple); letter-spacing: -0.5px;
  }
  .requirements ul { list-style: none; margin-top: 6px; white-space: nowrap;
    font-family: "Mulish", sans-serif; font-weight: 400; font-size: 26px; line-height: 23px;
    letter-spacing: 0.3px; color: var(--ink); }
  .requirements li { position: relative; padding-left: 36px; margin-bottom: 27px; }
  .requirements .tick { position: absolute; left: 0; top: 2px; width: 20px; height: 20px; }
</style>
</head>
<body>
<div class="flyer">
  <div class="hero-photo" role="img" aria-label="Photo of a tradesman in navy coveralls with a clipboard and tool belt, standing before a house under a blue sky and green lawn"></div>
  <div class="hero-band"></div>
  <div class="bottom-band"></div>

  <div class="brand-box">
    <span class="brand-dot"></span>
    <span class="brand-name">BRINDLE<br>ASSET MANAGEMENT</span>
  </div>

  <h1 class="headline">
    <div class="lead">JOIN OUR</div>
    <div class="key">TEAM</div>
  </h1>

  <div class="benefits-frame"></div>
  <div class="benefits-panel"></div>
  <ul class="benefits">
    <li><svg class="tick" viewBox="0 0 22 22"><rect x="1" y="3" width="18" height="18" fill="#fff" stroke="#111" stroke-width="2"/><path d="M5 12l4 4 11-13" fill="none" stroke="#111" stroke-width="3"/></svg>95% approval rating on all<br>submitted estimates.</li>
    <li><svg class="tick" viewBox="0 0 22 22"><rect x="1" y="3" width="18" height="18" fill="#fff" stroke="#111" stroke-width="2"/><path d="M5 12l4 4 11-13" fill="none" stroke="#111" stroke-width="3"/></svg>Guaranteed work volume.</li>
    <li><svg class="tick" viewBox="0 0 22 22"><rect x="1" y="3" width="18" height="18" fill="#fff" stroke="#111" stroke-width="2"/><path d="M5 12l4 4 11-13" fill="none" stroke="#111" stroke-width="3"/></svg>Material purchasing program to<br>help vendors with low capital or<br>no or bad credit.</li>
    <li><svg class="tick" viewBox="0 0 22 22"><rect x="1" y="3" width="18" height="18" fill="#fff" stroke="#111" stroke-width="2"/><path d="M5 12l4 4 11-13" fill="none" stroke="#111" stroke-width="3"/></svg>Weekly secure direct deposit.<br>with net 30 payment terms.</li>
  </ul>

  <div class="contact-label">CONTACT</div>
  <div class="phone-box">555-204-3817</div>
  <div class="web-bar">www.brindleassetmanagement.com</div>

  <section class="requirements">
    <h2>REQUIREMENTS TO<br>BECOME A VENDOR</h2>
    <ul>
      <li><svg class="tick" viewBox="0 0 22 22"><rect x="1" y="3" width="18" height="18" fill="#fff" stroke="#111" stroke-width="2"/><path d="M5 12l4 4 11-13" fill="none" stroke="#111" stroke-width="3"/></svg>Auto insurance</li>
      <li><svg class="tick" viewBox="0 0 22 22"><rect x="1" y="3" width="18" height="18" fill="#fff" stroke="#111" stroke-width="2"/><path d="M5 12l4 4 11-13" fill="none" stroke="#111" stroke-width="3"/></svg>Certificate of general liability<br>insurance</li>
      <li><svg class="tick" viewBox="0 0 22 22"><rect x="1" y="3" width="18" height="18" fill="#fff" stroke="#111" stroke-width="2"/><path d="M5 12l4 4 11-13" fill="none" stroke="#111" stroke-width="3"/></svg>Workman’s Compensation or state<br>issued exemption letter</li>
      <li><svg class="tick" viewBox="0 0 22 22"><rect x="1" y="3" width="18" height="18" fill="#fff" stroke="#111" stroke-width="2"/><path d="M5 12l4 4 11-13" fill="none" stroke="#111" stroke-width="3"/></svg>Drive License or state issued ID card</li>
      <li><svg class="tick" viewBox="0 0 22 22"><rect x="1" y="3" width="18" height="18" fill="#fff" stroke="#111" stroke-width="2"/><path d="M5 12l4 4 11-13" fill="none" stroke="#111" stroke-width="3"/></svg>Coverage area</li>
      <li><svg class="tick" viewBox="0 0 22 22"><rect x="1" y="3" width="18" height="18" fill="#fff" stroke="#111" stroke-width="2"/><path d="M5 12l4 4 11-13" fill="none" stroke="#111" stroke-width="3"/></svg>Any speciality Licenses</li>
    </ul>
  </section>
</div>
</body>
</html>
```